Business Cards Needed for Innovative Healthcare Marketing Company

We are a marketing company focused on healthcare. Our company is all about rebranding yourself renewing your image and generating results. The phoenix stands for "reborn" or "rising" which we provide new brands for our clients we take their old brands and renew it with creativity and innovation. I am looking for a business card with color dimension. I have attached an example of a card I think has the look and feel of what I am trying to accomplish. I like that the card example has black and grey font colors, I like the font placement and the small logo, I really like the use of the colors on the right those are the colors of my logo. My logo is phoenix so maybe incorporating flames similar to that design. I would like the back a solid color maybe red with an opaque version of the logo and website. As a marketing company I am always open to creative liberty!

Target Market(s)

Doctors and business professionals.

Industry/Entity Type

Marketing

Contact Information for Business Card

Valcorne Health Care Marketing
Marla Tenwick- CEO
#(512)638-2974
email-marla@valcorne.com
website- valcorne.com

Font styles to use
Sans Serif

Colors
ec1f27
f37122
ffc214
fbed22
fbf289
f04a50

Requirements
Must have
• The logo and required information
Nice to have
• icons by the information
Should not have
• child like font

```html
<!DOCTYPE html>
<html lang="en">
<head>
<meta charset="utf-8">
<title>Valcorne Health Care Marketing – Business Cards</title>
<link rel="stylesheet" href="https://fonts.googleapis.com/css2?family=Arvo:wght@400;700&family=Raleway:wght@200;300;400&display=swap">
<style>
  :root {
    --backdrop: #ece9e4;
    --card: #ffffff;
    --card-edge: #dcdcdc;
    --brand-red: #9b1c14;
    --brand-orange: #d9662b;
    --ink-grey: #7a7a7a;
    --ink-dark: #2a2a2a;
    --faint-grey: #d6d6d6;
    --mid-grey: #9a9a9a;
  }
  * { box-sizing: border-box; margin: 0; padding: 0; }
  html, body {
    width: 1200px; height: 913px; overflow: hidden;
    background: var(--backdrop);
  }
  .canvas { position: relative; width: 1200px; height: 913px; }
  .card {
    position: absolute; width: 540px; height: 309px;
    background: var(--card);
    box-shadow: 0 2px 0 var(--card-edge), 0 4px 0 #f4f4f4, 0 6px 0 var(--card-edge), 0 14px 28px rgba(0,0,0,.18);
    overflow: hidden;
  }
  /* back of card */
  .card-back { left: 30px; top: 302px; }
  .back-mark {
    position: absolute; left: 52px; top: 84px;
    width: 140px; height: 140px; border-radius: 50%;
    background: #f1f1f1;
  }
  .back-name {
    position: absolute; left: 218px; top: 104px; width: 290px;
    font-family: 'Raleway', sans-serif; font-weight: 200;
    color: var(--faint-grey);
  }
  .back-name .name-main { display: block; font-size: 50px; letter-spacing: 2px; line-height: 1; }
  .back-name .name-sub {
    display: block; margin-top: 8px; padding-top: 6px;
    border-top: 1px solid var(--faint-grey);
    font-size: 13px; letter-spacing: 2px; text-transform: uppercase;
  }
  .back-url {
    position: absolute; right: 40px; bottom: 64px;
    font-family: 'Arvo', serif; font-size: 22px; color: var(--mid-grey);
  }
  .back-url .url-brand { color: var(--brand-red); font-weight: 700; }

  /* front of card */
  .card-front { left: 630px; top: 302px; }
  .front-pattern { position: absolute; inset: 0; }
  .front-logo {
    position: absolute; left: 30px; top: 104px;
    display: flex; align-items: center; gap: 10px;
  }
  .front-logo .logo-dot { width: 40px; height: 40px; border-radius: 50%; background: var(--brand-orange); }
  .front-logo .logo-name {
    font-family: 'Raleway', sans-serif; font-weight: 400; font-size: 13px;
    color: var(--brand-orange); line-height: 1.2; letter-spacing: .5px;
  }
  .front-identity { position: absolute; left: 32px; top: 168px; }
  .person-name {
    font-family: 'Arvo', serif; font-weight: 700; font-size: 24px;
    color: var(--brand-red); line-height: 1.1;
  }
  .person-role {
    font-family: 'Raleway', sans-serif; font-size: 14px; color: var(--ink-grey);
  }
  .contact-list { position: absolute; left: 32px; top: 230px; list-style: none; }
  .contact-item {
    display: flex; align-items: center; gap: 8px;
    font-family: 'Arvo', serif; font-size: 14px; color: var(--ink-dark);
    height: 22px;
  }
  .contact-icon { width: 16px; height: 16px; flex: none; }
</style>
</head>
<body>
<main class="canvas">

  <section class="card card-back" aria-label="Card back">
    <div class="back-mark"></div>
    <div class="back-name">
      <span class="name-main">VALCORNE</span>
      <span class="name-sub">Health Care Marketing</span>
    </div>
    <p class="back-url">www.<span class="url-brand">valcorne</span>.com</p>
  </section>

  <section class="card card-front" aria-label="Card front">
    <svg class="front-pattern" viewBox="0 0 540 309" preserveAspectRatio="none">
      <defs>
        <linearGradient id="facet-tones" x1="0" y1="1" x2="1" y2="0">
          <stop offset="0" stop-color="#ec1f27"/>
          <stop offset=".2" stop-color="#f37122"/>
          <stop offset=".35" stop-color="#ffc214"/>
          <stop offset=".55" stop-color="#b7aed8"/>
          <stop offset=".8" stop-color="#d9a3cc"/>
          <stop offset="1" stop-color="#eee6f0"/>
        </linearGradient>
      </defs>
      <polygon role="img" aria-label="Colourful faceted triangle pattern in red, orange, yellow, lilac and pink"
        fill="url(#facet-tones)"
        points="300,0 540,0 540,309 345,309 300,230 262,150 248,70"/>
    </svg>

    <div class="front-logo">
      <span class="logo-dot"></span>
      <span class="logo-name">VALCORNE<br>Health Care Marketing</span>
    </div>

    <div class="front-identity">
      <p class="person-name">Marla TENWICK</p>
      <p class="person-role">CEO</p>
    </div>

    <ul class="contact-list">
      <li class="contact-item">
        <svg class="contact-icon" viewBox="0 0 16 16"><circle cx="8" cy="8" r="8" fill="#9b1c14"/><path d="M5.2 4.2l1.4 1.6-.8 1c.5 1.2 1.3 2 2.5 2.5l1-.8 1.6 1.4-.9 1.3C7.6 11 5 8.4 4.8 5.1z" fill="#fff"/></svg>
        (512)638-2974
      </li>
      <li class="contact-item">
        <svg class="contact-icon" viewBox="0 0 16 16"><circle cx="8" cy="8" r="8" fill="#9b1c14"/><rect x="4" y="5" width="8" height="6" fill="none" stroke="#fff" stroke-width="1"/><path d="M4 5l4 3.4L12 5" fill="none" stroke="#fff" stroke-width="1"/></svg>
        marla@valcorne.com
      </li>
      <li class="contact-item">
        <svg class="contact-icon" viewBox="0 0 16 16"><circle cx="8" cy="8" r="8" fill="#9b1c14"/><circle cx="8" cy="8" r="4.2" fill="none" stroke="#fff" stroke-width="1"/><path d="M3.8 8h8.4M8 3.8c-2 2.4-2 6 0 8.4M8 3.8c2 2.4 2 6 0 8.4" fill="none" stroke="#fff" stroke-width=".8"/></svg>
        valcorne.com
      </li>
    </ul>
  </section>

</main>
</body>
</html>
```